I need a business card design for a new dance business. I offer classical Indian dance tuition and also professional performances. I want to offer the community a variety of Indian dance experiences which include: group class and private tuition, school and preschool educational courses and workshops. dance theatre performances, community function workshops and performances, Kids Bollywood parties, wedding & conference performances, mouth percussion classes, Indian mythology/ dance costume and make up workshops.
The final design should communicate a feeling and impression of the vibrance and energy of Indian dance.
Updates
Hi Everyone,
Project Deadline Extended
Reason: I would like to refine a few changes to the details of this lovely design and we have run out of time!
Project Deadline Extended
Reason: Still waiting to hear back form designer re two possible changes to the card design. Tomorrow is the deadline and I have sent several messages but with no response. I need to see this through before selecting this lovely design.
Thank you.
Tara
Industry/Entity Type
Preschool
Requirements
Must have
- The front of the business card should have the photo of me (my face and torso), surrounded entirely by a border of bright magenta (to match the magenta of my lipstick - it is the same as the magenta on my skirt in the second photo). Within the top border I want (perhaps yellow-gold) writing to say "Tara Holloway - Artistic Director" and within the bottom border it should read "Saffron Lantern Indian Dance." If you turn the card on its side the left border should have my telephone number: 0417 862 493 and the right-hand border should read: saffronlanternindiandance@quillmail.example
The reverse of the card should be the orange of the dance costume
and I'd like the picture of my feet and legs to be on the right side of the back of the card as a side border. Centre-aligned on the orange background it should read (perhaps in dark magenta):
Indian dance classes + private tuition
School + preschool educational courses and workshops
Dance theatre performances
Community function workshops and performances
Children's Bollywood parties
Wedding + conference performances
Mouth percussion classes
Indian mythology and dance demonstration workshops
Dance costume and make-up workshops
Nice to have
- A lovely artistic but easy-to-read font would be nice.

```html
<!DOCTYPE html>
<html lang="en">
<head>
<meta charset="utf-8">
<title>Saffron Lantern Indian Dance – Business Card</title>
<link href="https://fonts.googleapis.com/css2?family=Lobster&family=Alegreya:wght@400;500&family=Cabin:wght@400;500&display=swap" rel="stylesheet">
<style>
  :root {
    --saffron: #e07e2c;
    --plum: #62296f;
    --dark-magenta: #7a1f5c;
    --magenta: #c2267f;
    --gold: #f2c14e;
    --white: #ffffff;
    --paper: #ffffff;
  }
  * { margin: 0; padding: 0; box-sizing: border-box; }
  html, body { width: 1200px; height: 900px; overflow: hidden; background: var(--paper); }
  .sheet { position: relative; width: 1200px; height: 900px; }
  .card { position: absolute; top: 84px; width: 450px; height: 742px; overflow: hidden; }

  /* Front: portrait framed by a magenta border */
  .card--front { left: 108px; background: var(--magenta); }
  .front__portrait {
    position: absolute; left: 54px; top: 62px; right: 54px; bottom: 62px;
    background: linear-gradient(180deg, #8a3a6a 0%, #d9923a 45%, #e7a844 70%, #a3284f 100%);
  }
  .front__title, .front__brand {
    position: absolute; left: 0; width: 450px; text-align: center; color: var(--gold);
  }
  .front__title {
    top: 16px; font-family: "Alegreya", serif; font-weight: 500; font-size: 24px; line-height: 30px;
  }
  .front__brand {
    bottom: 12px; font-family: "Lobster", cursive; font-size: 30px; line-height: 38px;
  }
  .front__side {
    position: absolute; top: 62px; height: 618px; width: 54px;
    display: flex; align-items: center; justify-content: center;
    writing-mode: vertical-rl; color: var(--gold); white-space: nowrap;
    font-family: "Cabin", sans-serif; font-weight: 500;
  }
  .front__side--phone { left: 0; transform: rotate(180deg); font-size: 28px; letter-spacing: 1px; }
  .front__side--email { right: 0; font-size: 21px; }

  /* Back: orange with services and a photo strip on the right */
  .card--back { left: 623px; background: var(--saffron); }
  .back__strip {
    position: absolute; right: 0; top: 0; width: 120px; height: 742px;
    background: linear-gradient(180deg, #5a1c3c 0%, var(--magenta) 30%, #d8a03f 55%, #b5306f 78%, #c8323a 100%);
  }
  .back__services {
    position: absolute; left: 22px; top: 40px; width: 288px; height: 662px;
    list-style: none; display: flex; flex-direction: column; justify-content: space-between;
    font-family: "Alegreya", serif; font-weight: 500; font-size: 23px; line-height: 28px;
    color: var(--dark-magenta); text-align: center;
  }
</style>
</head>
<body>
<main class="sheet">
  <section class="card card--front">
    <p class="front__title">Tara Holloway – Artistic Director</p>
    <div class="front__portrait" role="img" aria-label="Portrait photo of the dancer, face and torso, in gold costume"></div>
    <p class="front__side front__side--phone">0417 862 493</p>
    <p class="front__side front__side--email">saffronlanternindiandance@quillmail.example</p>
    <h1 class="front__brand">Saffron Lantern Indian Dance</h1>
  </section>

  <section class="card card--back">
    <ul class="back__services">
      <li>Indian dance classes + private tuition</li>
      <li>School + preschool educational courses and workshops</li>
      <li>Dance theatre performances</li>
      <li>Community function workshops and performances</li>
      <li>Children's Bollywood parties</li>
      <li>Wedding + conference performances</li>
      <li>Mouth percussion classes</li>
      <li>Indian mythology and dance demonstration workshops</li>
      <li>Dance costume and make-up workshops</li>
    </ul>
    <div class="back__strip" role="img" aria-label="Photo of the dancer's legs and feet in magenta and gold silk with ankle bells"></div>
  </section>
</main>
</body>
</html>
```